New Fun, Positive, energised looking Business Card Needed for High Achiever Coach

I am looking for a two sided full colour business card. I am self employed and have recently re branded my 1-2-1 work re-vitalising high achievers. My target client base for these cards is therefore high achievers - usually aged 40 -55, they are often entrepreneurs, CEO or work in banking and finance and 2/3 are male. I work with them on 90 day or 6 month coaching programs to help them live their success in a healthier, more sustainable and fulfiiled way. They pay for this privately so though they are corporate types the cards need not look 'corporate'. I want to portray the idea of transformation, vitality and re-connecting.
You can get a feel for the look I like on my new website: morvenlisk.co.uk
I want to use this logo with strapline (Re-Vitalising High Achievers) (I purchased off Logoharbor) and font/ colours (the turquoise and green).
Details to include on the card:
www.morvenlisk.co.uk
+44 7915 302618
morven@morvenlisk.co.uk
skype: morvenlisk
I'd also like to include:
Do you struggle to switch off? Want to be healthier and feel fitter? Want closer relationships? More clarity over the direction you are headed? I can help you do these things using integrated mind-body techniques. Visit morvenlisk.co.uk TODAY to apply for a FREE Breakthrough session.
BUT if that is too much text for a card I am open to advice/ammendments.
Updates
Thanks for your design - I am considering them. PLease change the wording to :

```html
<!DOCTYPE html>
<html lang="en">
<head>
<meta charset="utf-8">
<title>Morven Lisk – Business Card</title>
<link rel="stylesheet" href="https://fonts.googleapis.com/css2?family=Open+Sans:wght@400;600;700;800&display=swap">
<style>
  :root {
    --turquoise: #0ea5c9;
    --turquoise-deep: #0b93b6;
    --green: #5cb85c;
    --white: #ffffff;
    --backdrop: #e6e8ea;
    --card-shadow: rgba(0, 0, 0, 0.18);
  }
  * { box-sizing: border-box; margin: 0; padding: 0; }
  html, body {
    width: 1200px;
    height: 987px;
    overflow: hidden;
    background: var(--backdrop);
    font-family: "Open Sans", Arial, sans-serif;
  }
  .stage {
    width: 1200px;
    height: 987px;
    display: flex;
    align-items: center;
    justify-content: center;
    gap: 40px;
  }
  .card {
    position: relative;
    width: 560px;
    height: 320px;
    border-radius: 28px;
    overflow: hidden;
    box-shadow: 0 12px 30px var(--card-shadow);
  }

  /* Front */
  .card-front { background: var(--white); }
  .front-wave { position: absolute; inset: 0; width: 100%; height: 100%; }
  .brand {
    position: absolute;
    left: 150px;
    top: 62px;
    display: flex;
    flex-direction: column;
    align-items: flex-start;
  }
  .brand-row { display: flex; align-items: center; gap: 12px; }
  .brand-dot {
    width: 34px; height: 34px;
    border-radius: 50%;
    background: var(--green);
  }
  .brand-name {
    font-weight: 800;
    font-size: 34px;
    color: var(--turquoise);
    letter-spacing: 0.5px;
  }
  .brand-strapline {
    margin-top: 4px;
    margin-left: 46px;
    font-size: 14px;
    font-weight: 400;
    color: var(--turquoise-deep);
  }
  .website {
    position: absolute;
    left: 28px;
    bottom: 26px;
    font-size: 16px;
    font-weight: 600;
    color: var(--white);
    letter-spacing: 1.5px;
  }
  .contacts {
    position: absolute;
    right: 30px;
    bottom: 20px;
    list-style: none;
    color: var(--white);
    font-size: 17px;
    line-height: 26px;
  }
  .contacts li { display: flex; align-items: center; gap: 8px; }
  .contact-icon { width: 16px; height: 16px; flex: none; }

  /* Back */
  .card-back {
    background: var(--turquoise);
    display: flex;
    flex-direction: column;
    align-items: center;
    justify-content: center;
    text-align: center;
    color: var(--white);
    padding: 0 30px;
  }
  .pitch { font-size: 19px; line-height: 25px; }
  .pitch + .pitch { margin-top: 10px; }
  .pitch strong { font-weight: 700; }
</style>
</head>
<body>
<main class="stage">

  <section class="card card-front" aria-label="Card front">
    <svg class="front-wave" viewBox="0 0 560 320" preserveAspectRatio="none" aria-hidden="true">
      <path d="M0,118 C30,196 130,196 270,202 C400,208 500,206 560,196 L560,320 L0,320 Z" fill="var(--turquoise)"/>
      <path d="M0,104 C34,182 140,184 276,190 C404,196 500,192 560,182" fill="none" stroke="var(--green)" stroke-width="4"/>
    </svg>

    <div class="brand">
      <div class="brand-row">
        <span class="brand-dot"></span>
        <span class="brand-name">Morven Lisk</span>
      </div>
      <span class="brand-strapline">Re-Vitalising High Achievers</span>
    </div>

    <p class="website">www.morvenlisk.co.uk</p>

    <ul class="contacts">
      <li>
        <svg class="contact-icon" viewBox="0 0 16 16" aria-hidden="true">
          <circle cx="8" cy="8" r="7.2" fill="none" stroke="#fff" stroke-width="1.4"/>
          <path d="M5.2,4.4 L6.6,4.2 L7.3,6 L6.4,6.8 C6.9,7.9 7.9,8.9 9,9.4 L9.8,8.5 L11.6,9.2 L11.4,10.6 C8,11 4.8,7.8 5.2,4.4 Z" fill="#fff"/>
        </svg>
        +44 7915 302618
      </li>
      <li>
        <svg class="contact-icon" viewBox="0 0 16 16" aria-hidden="true">
          <rect x="1" y="3.5" width="14" height="9.5" rx="1.2" fill="#fff"/>
          <path d="M1.5,4.2 L8,9 L14.5,4.2" fill="none" stroke="var(--turquoise)" stroke-width="1.2"/>
        </svg>
        morven@morvenlisk.co.uk
      </li>
      <li>
        <svg class="contact-icon" viewBox="0 0 16 16" aria-hidden="true">
          <rect x="1" y="1" width="14" height="14" rx="3" fill="#fff"/>
        </svg>
        morvenlisk
      </li>
    </ul>
  </section>

  <section class="card card-back" aria-label="Card back">
    <p class="pitch">
      Do you struggle to switch off?<br>
      Want to be healthier and feel fitter?<br>
      Want closer relationships?<br>
      More clarity over the direction you are headed?<br>
      I can help you do these things using integrated<br>
      mind-body techniques.
    </p>
    <p class="pitch">
      Visit <strong>morvenlisk.co.uk</strong> TODAY to apply for a<br>
      FREE Breakthrough session.
    </p>
  </section>

</main>
</body>
</html>
```